TalkHarbor - Language Coaching Services

Sleek, innovative, trendy design for Language Coaching business.

TalkHarbor is a new UK based company that provides Language Coaching services. We offer highly personalized on-line and face to face language courses. We also impart learning techniques workshops based on the latest neuroscience research for second-language acquisition.

Target Market(s)

See attached info

Industry/Entity Type

Consulting

Contact Information for Business Card

TalkHarbor
DaniaKV@talkharbor.co.uk
TalkHarbor.co.uk
London, UK

Font styles to use
Sans Serif

```html
<!DOCTYPE html>
<html lang="en">
<head>
<meta charset="utf-8">
<title>TalkHarbor – Business Card</title>
<link rel="stylesheet" href="https://fonts.googleapis.com/css2?family=Montserrat:wght@300;400;600&display=swap">
<style>
  :root {
    --bg: #d9d9d9;
    --brand-blue: #0a80b5;
    --brand-blue-deep: #0673a6;
    --brand-blue-bright: #1592cc;
    --card-dark: #1a1b1d;
    --white: #ffffff;
    --rule: #e6f2f8;
  }
  * { box-sizing: border-box; margin: 0; padding: 0; }
  html, body {
    width: 1125px;
    height: 1200px;
    overflow: hidden;
    background: var(--bg);
    font-family: "Montserrat", "Helvetica Neue", Arial, sans-serif;
  }
  .canvas { position: relative; width: 1125px; height: 1200px; }
  .card {
    position: absolute;
    left: 150px;
    width: 825px;
    height: 471px;
    border-radius: 26px;
    overflow: hidden;
  }
  .card--front { top: 98px; background: var(--brand-blue); }
  .card--back  { top: 631px; background: var(--card-dark); }

  .front-panel { position: absolute; inset: 0; width: 100%; height: 100%; }

  .front-text {
    position: absolute;
    right: 55px;
    white-space: nowrap;
    text-align: right;
    color: var(--white);
    line-height: 1;
  }
  .person-name {
    top: 172px;
    font-size: 28px;
    font-weight: 600;
    letter-spacing: 1.2px;
  }
  .person-role {
    top: 206px;
    font-size: 19px;
    font-weight: 600;
    letter-spacing: 1px;
  }
  .contact-rule {
    position: absolute;
    right: 55px;
    top: 246px;
    width: 230px;
    height: 3px;
    background: var(--rule);
  }
  .contact-list { list-style: none; top: 271px; }
  .contact-item {
    display: flex;
    justify-content: flex-end;
    align-items: center;
    gap: 10px;
    font-size: 18px;
    font-weight: 300;
    height: 26px;
  }
  .contact-icon { width: 17px; height: 17px; flex: none; }

  .wordmark {
    position: absolute;
    font-weight: 400;
    line-height: 1;
    white-space: nowrap;
  }
  .wordmark--front {
    right: 55px;
    top: 372px;
    font-size: 54px;
    letter-spacing: 0.5px;
    color: var(--white);
  }

  .back-emblem {
    position: absolute;
    left: 334px;
    top: 126px;
    width: 156px;
    height: 156px;
    border: 8px solid var(--brand-blue-bright);
    border-radius: 50%;
  }
  .wordmark--back {
    left: 0;
    right: 0;
    top: 294px;
    text-align: center;
    font-size: 56px;
    letter-spacing: 0.5px;
    color: var(--brand-blue-bright);
  }
</style>
</head>
<body>
<main class="canvas">

  <section class="card card--front" aria-label="Business card front">
    <svg class="front-panel" viewBox="0 0 825 471" preserveAspectRatio="none" aria-hidden="true">
      <path d="M0 0 H270 Q430 235 300 471 H0 Z" fill="var(--brand-blue-deep)" opacity="0.55"/>
      <path d="M0 0 H220 Q390 235 250 471 H0 Z" fill="var(--white)"/>
    </svg>

    <h1 class="front-text person-name">OWEN HARTLEY</h1>
    <p class="front-text person-role">CEO/FOUNDER</p>
    <div class="contact-rule"></div>
    <ul class="front-text contact-list">
      <li class="contact-item">624 518 3907
        <svg class="contact-icon" viewBox="0 0 16 16" aria-hidden="true"><rect x="4" y="1" width="8" height="14" rx="1.5" fill="none" stroke="#fff" stroke-width="1.5"/><circle cx="8" cy="12.5" r="0.9" fill="#fff"/></svg>
      </li>
      <li class="contact-item">Info@talkharbor.co.uk
        <svg class="contact-icon" viewBox="0 0 16 16" aria-hidden="true"><rect x="1" y="3.5" width="14" height="9" rx="1" fill="#fff"/><path d="M1.5 4 L8 9 L14.5 4" fill="none" stroke="var(--brand-blue)" stroke-width="1.2"/></svg>
      </li>
      <li class="contact-item">www.talkharbor.co.uk
        <svg class="contact-icon" viewBox="0 0 16 16" aria-hidden="true"><circle cx="8" cy="8" r="7" fill="#fff"/><ellipse cx="8" cy="8" rx="3" ry="7" fill="none" stroke="var(--brand-blue)" stroke-width="1"/><path d="M1 8 H15" stroke="var(--brand-blue)" stroke-width="1"/></svg>
      </li>
    </ul>

    <p class="wordmark wordmark--front">TALKHARBOR</p>
  </section>

  <section class="card card--back" aria-label="Business card back">
    <div class="back-emblem" aria-hidden="true"></div>
    <p class="wordmark wordmark--back">TALKHARBOR</p>
  </section>

</main>
</body>
</html>
```